Heron Loan Partners Business Card

We need a business card design for our mortgage servicing company. In addition to servicing the loans of homeowners, we help homeowners with purchasing their homes and any mortgage refinancing. We would like to see designs that use the colors in the logo attached below (gold-ish yellow and navy blue), and any other design you deem fit! The design should communicate a simpler life with smart mortgages provided by Heron.

```html
<!DOCTYPE html>
<html lang="en">
<head>
<meta charset="utf-8">
<title>Heron Loan Partners Business Card</title>
<link rel="stylesheet" href="https://fonts.googleapis.com/css2?family=Montserrat:wght@400;500;700&display=swap">
<style>
  :root {
    --stage: #454545;
    --paper: #ffffff;
    --navy: #252155;
    --gold: #e1b23c;
    --ink: #141414;
  }
  * { box-sizing: border-box; margin: 0; padding: 0; }
  html, body { width: 1200px; height: 1200px; overflow: hidden; }
  body {
    background: var(--stage);
    font-family: "Montserrat", Arial, sans-serif;
    position: relative;
  }
  .card {
    position: absolute;
    left: 193px;
    width: 818px;
    height: 464px;
    border-radius: 22px;
    overflow: hidden;
  }
  .card--front { top: 174px; background: var(--paper); }
  .card--back { top: 684px; background: var(--navy); }

  .holder { position: absolute; left: 47px; top: 70px; }
  .holder__name {
    font-weight: 700; font-size: 22px; letter-spacing: 0.2px;
    color: var(--navy); line-height: 1.2;
  }
  .holder__name .surname { color: var(--gold); }
  .holder__role { font-size: 19px; color: var(--ink); margin-top: 4px; }

  .brand-name {
    position: absolute;
    color: var(--gold);
    font-weight: 700;
    line-height: 1.05;
    display: flex;
    align-items: center;
  }
  .brand-name__dot {
    display: inline-block; border-radius: 50%; background: var(--gold);
  }
  .card--front .brand-name { right: 56px; top: 62px; font-size: 30px; gap: 14px; }
  .card--front .brand-name__dot { width: 22px; height: 22px; }
  .card--back .brand-name {
    left: 0; right: 0; top: 0; bottom: 0; justify-content: center;
    font-size: 60px; gap: 22px;
  }
  .card--back .brand-name__dot { width: 40px; height: 40px; }

  .contact { position: absolute; left: 45px; top: 270px; list-style: none; }
  .contact__item {
    display: flex; align-items: center; gap: 11px;
    font-size: 19px; color: var(--ink); height: 32.5px;
  }
  .contact__icon { width: 20px; height: 20px; flex: none; }

  .address {
    position: absolute; left: 535px; top: 292px;
    font-size: 19.5px; line-height: 29px; color: var(--ink); font-style: normal;
  }
  .wave { position: absolute; left: 0; top: 0; width: 818px; height: 464px; }
</style>
</head>
<body>
  <section class="card card--front">
    <svg class="wave" viewBox="0 0 818 464" aria-hidden="true">
      <path d="M0 365 C 80 400, 180 410, 300 398 C 470 380, 620 340, 740 360 C 780 367, 805 378, 818 386 L818 380 C 790 362, 760 352, 720 350 C 600 342, 450 378, 300 388 C 170 396, 80 382, 0 360 Z" fill="var(--gold)"/>
      <path d="M0 380 C 80 408, 180 420, 300 412 C 460 398, 620 364, 740 372 C 780 375, 805 383, 818 390 L818 464 L0 464 Z" fill="var(--navy)"/>
    </svg>

    <div class="holder">
      <p class="holder__name">DANA <span class="surname">WELLER</span></p>
      <p class="holder__role">Owner</p>
    </div>

    <div class="brand-name"><span class="brand-name__dot"></span><span>Heron Loan<br>Partners</span></div>

    <ul class="contact">
      <li class="contact__item">
        <svg class="contact__icon" viewBox="0 0 20 20" aria-hidden="true"><path d="M2 7 C2 3, 18 3, 18 7 L15 8.5 L14 6.5 C12 5.8, 8 5.8, 6 6.5 L5 8.5 Z" fill="var(--gold)"/><rect x="4" y="9" width="12" height="8" rx="1.5" fill="var(--gold)"/><circle cx="10" cy="13" r="2.2" fill="var(--paper)"/></svg>
        <span>555.204.7781</span>
      </li>
      <li class="contact__item">
        <svg class="contact__icon" viewBox="0 0 20 20" aria-hidden="true"><rect x="1" y="4" width="18" height="12" fill="var(--gold)"/><path d="M1 4 L10 11 L19 4 M1 16 L7.5 9.5 M19 16 L12.5 9.5" stroke="var(--paper)" stroke-width="1.2" fill="none"/></svg>
        <span>info@heronloanpartners.com</span>
      </li>
      <li class="contact__item">
        <svg class="contact__icon" viewBox="0 0 20 20" aria-hidden="true"><circle cx="10" cy="10" r="9" fill="var(--gold)"/><path d="M4 6 C7 5, 8 8, 6 10 C5 12, 8 14, 7 17 M12 3 C11 6, 14 7, 16 6 M12 12 C14 11, 17 13, 15 16" stroke="var(--paper)" stroke-width="1.4" fill="none"/></svg>
        <span>www.heronloanpartners.com</span>
      </li>
    </ul>

    <address class="address">4820 Alder Bend Rd, Ste<br>210, Austin, TX 78701</address>
  </section>

  <section class="card card--back">
    <div class="brand-name"><span class="brand-name__dot"></span><span>Heron Loan Partners</span></div>
  </section>
</body>
</html>
```